Business Card for Professional Photographer

I'm looking for an eye catching modern clean design that compliments my logo/ website fonts & colours.
I specialise in architecture, corporate & commercial photography so I'm marketing to professional clients rather than portrait / wedding clients.

I would prefer to not have a solid black design.

My logo brand guide is as follows :

Main front font. : Reislust
Main font colour : #fff
Slogan front font : Ubuntu Bold
Monogram front font : Venti Medium
Container colour : #fff

I need print ready files in pdf .png & .eps formats.

Included in the files below are some screen grabs as reference to font & colours etc.

```html
<!DOCTYPE html>
<html lang="en">
<head>
<meta charset="utf-8">
<title>Northlight Studio – Business Card</title>
<link href="https://fonts.googleapis.com/css2?family=Open+Sans:wght@400;700&display=swap" rel="stylesheet">
<style>
  :root{
    --backdrop:#d9d9d6;
    --card:#262626;
    --gold:#c9a24a;
    --gold-light:#e3c57a;
    --white:#ffffff;
  }
  *{margin:0;padding:0;box-sizing:border-box}
  html,body{width:1200px;height:913px;overflow:hidden}
  body{
    background:var(--backdrop);
    display:flex;align-items:center;justify-content:center;gap:40px;
    font-family:"Open Sans",Arial,sans-serif;
  }
  .card{
    position:relative;width:540px;height:309px;
    background:var(--card);border-radius:18px;
    box-shadow:0 10px 24px rgba(0,0,0,.25);
    color:var(--white);
  }
  .brand{display:flex;align-items:center;gap:12px;white-space:nowrap}
  .brand-mark{width:14px;height:14px;background:var(--gold);flex:none}
  .brand-text{display:flex;flex-direction:column}
  .brand-name{
    font-family:"Open Sans",Arial,sans-serif;font-weight:400;
    color:var(--white);font-size:24px;line-height:1;letter-spacing:.02em;
  }
  .brand-tagline{
    font-family:"Open Sans",Arial,sans-serif;font-weight:400;
    color:var(--gold);font-size:10px;margin-top:6px;letter-spacing:.03em;
  }
  .card-front .brand{position:absolute;left:50%;top:50%;transform:translate(-50%,-50%)}
  .card-back .brand{position:absolute;right:40px;top:40px}
  .card-back .brand-name{font-size:19px}
  .card-back .brand-tagline{font-size:9px}
  .card-back .brand-mark{width:12px;height:12px}
  .divider{
    position:absolute;left:40px;right:40px;top:150px;height:1px;
    background:linear-gradient(90deg,var(--gold-light),var(--gold));
  }
  .person{position:absolute;left:40px;top:168px}
  .person-name{font-weight:700;color:var(--gold);font-size:20px;letter-spacing:.02em;line-height:1.1}
  .person-role{font-size:13px;margin-top:2px}
  .person-rule{width:150px;height:1px;background:var(--gold);margin:9px 0 7px}
  .contacts{list-style:none;font-size:12.5px;line-height:1.6}
  .contacts li{display:flex;align-items:center;gap:8px}
  .contacts svg{width:12px;height:12px;flex:none}
  .address{position:absolute;right:40px;bottom:40px;text-align:right;font-size:13px;line-height:1.5;font-style:normal}
</style>
</head>
<body>
  <section class="card card-front">
    <div class="brand">
      <span class="brand-mark"></span>
      <div class="brand-text">
        <span class="brand-name">Northlight Studio</span>
        <span class="brand-tagline">Buildings · Business · Brands</span>
      </div>
    </div>
  </section>

  <section class="card card-back">
    <div class="brand">
      <span class="brand-mark"></span>
      <div class="brand-text">
        <span class="brand-name">Northlight Studio</span>
        <span class="brand-tagline">Buildings · Business · Brands</span>
      </div>
    </div>
    <div class="divider"></div>
    <div class="person">
      <div class="person-name">DANIEL ROWE</div>
      <div class="person-role">Director</div>
      <div class="person-rule"></div>
      <ul class="contacts">
        <li><svg viewBox="0 0 12 12"><path fill="#c9a24a" d="M2.5 1h2l1 3-1.4 1a6 6 0 0 0 2.9 2.9l1-1.4 3 1v2a1.5 1.5 0 0 1-1.5 1.5A9.5 9.5 0 0 1 1 2.5 1.5 1.5 0 0 1 2.5 1z"/></svg>555 204 3187</li>
        <li><svg viewBox="0 0 12 12"><rect x="0.5" y="2" width="11" height="8" rx="1" fill="#c9a24a"/><path d="M1 2.5l5 4 5-4" stroke="#262626" fill="none"/></svg>info@northlightstudio.com</li>
        <li><svg viewBox="0 0 12 12"><circle cx="6" cy="6" r="5.5" fill="#c9a24a"/><path d="M.5 6h11M6 .5c-3 3-3 8 0 11M6 .5c3 3 3 8 0 11" stroke="#262626" stroke-width=".8" fill="none"/></svg>www.northlightstudio.com</li>
      </ul>
    </div>
    <address class="address">48 Harbor Street<br>Portland ME 04101</address>
  </section>
</body>
</html>
```